Business Card Design

I am a realtor and i also flip houses. I am CEO and Founder of my business which is Voskell Group LLC which is named after my great uncle who died and i was really close to. He was a wonderful friendly man so i want my business to represent him too. My business works with a lot of different people but i want mainly something to show i am a strong confidant woman who owns there own business. I have a really fun personality so i don't want anything TOO serious or manly. I want the perfect mix. My last two business cards i created are too embarrassing to hand out because they are far too girly and i deal with a lot of millionaire clients. I live out in the Palm Springs California area. I think its very important to show i am a single mom, female with her own business at only 24. I don't want to just be a female that blends in with all of the other serious people but yet i don't want to seem immature. People are telling me to stay away from pinks and purples but i don't want blues and greens because they represent men more. But i won't say no to them if there is a happy medium.

Industry/Entity Type

Realtor

Contact Information for Business Card

Voskell Group, LLC
Corinne Tabb
27358 Halvern Ave, C2 517
Desert Linden, CA 92418
760-419-6735
Corinnedtabb@mailvane.com

```html
<!DOCTYPE html>
<html lang="en">
<head>
<meta charset="utf-8">
<title>Voskell Group LLC – Corinne Tabb</title>
<link rel="stylesheet" href="https://fonts.googleapis.com/css2?family=Aldrich&display=swap">
<style>
  :root {
    --blush: #f8b2d6;
    --mauve: #b6a6bd;
    --teal: #2f8a95;
    --teal-ink: #2f8c97;
    --lemon: #f4f27a;
  }
  html, body {
    margin: 0;
    padding: 0;
    width: 1200px;
    height: 702px;
    overflow: hidden;
  }
  .card {
    position: relative;
    width: 1200px;
    height: 702px;
    background: linear-gradient(90deg, var(--blush) 0%, var(--mauve) 40%, var(--teal) 100%);
    font-family: "Aldrich", sans-serif;
    color: var(--lemon);
  }
  .company {
    position: absolute;
    left: 64px;
    top: 318px;
    margin: 0;
    font-size: 46px;
    font-weight: 400;
    color: var(--teal-ink);
    letter-spacing: 3.5px;
  }
  .agent-name {
    position: absolute;
    left: 645px;
    top: 200px;
    margin: 0;
    font-size: 52px;
    font-weight: 400;
    letter-spacing: 3.3px;
  }
  .address {
    position: absolute;
    left: 647px;
    top: 290px;
    margin: 0;
    font-style: normal;
    font-size: 32px;
    line-height: 64px;
    letter-spacing: 2px;
  }
  .contact {
    position: absolute;
    left: 312px;
    top: 528px;
    margin: 0;
    padding: 0;
    list-style: none;
    font-size: 32px;
  }
  .contact-item {
    display: flex;
    align-items: center;
    height: 70px;
  }
  .contact-icon {
    width: 46px;
    height: 46px;
    fill: var(--teal-ink);
    flex: none;
  }
  .contact-phone .contact-icon { margin-right: 30px; }
  .contact-phone span { letter-spacing: 3.4px; }
  .contact-email .contact-icon { margin-right: 42px; }
</style>
</head>
<body>
<main class="card">
  <h2 class="company">Voskell Group LLC</h2>
  <h1 class="agent-name">Corinne Tabb</h1>
  <address class="address">
    27358 Halvern Ave<br>
    C2 517 Desert Linden<br>
    CA 92418
  </address>
  <ul class="contact">
    <li class="contact-item contact-phone">
      <svg class="contact-icon" viewBox="0 0 24 24" aria-hidden="true">
        <path d="M6.6 10.8c1.4 2.8 3.8 5.1 6.6 6.6l2.2-2.2c.3-.3.7-.4 1-.2 1.1.4 2.3.6 3.6.6.6 0 1 .4 1 1V20c0 .6-.4 1-1 1C10.6 21 3 13.4 3 4c0-.6.4-1 1-1h3.5c.6 0 1 .4 1 1 0 1.3.2 2.5.6 3.6.1.3 0 .7-.2 1z"/>
      </svg>
      <span>760-419-6735</span>
    </li>
    <li class="contact-item contact-email">
      <svg class="contact-icon" viewBox="0 0 24 24" aria-hidden="true">
        <path d="M2 5h20v14H2z M3.5 6.5v.3L12 13l8.5-6.2v-.3z M3.5 8.7v8.1l5.3-4.2z M20.5 8.7l-5.3 3.9 5.3 4.2z M10.1 13.6l-6.6 5v-.1h17v.1l-6.6-5L12 15z" fill-rule="evenodd"/>
      </svg>
      <span>corinnedtabb@mailvane.com</span>
    </li>
  </ul>
</main>
</body>
</html>
```